CFO services graphic design

I own a business consulting firm called Thornfield Advisory and we need a graphic for CFO services in our colours and branding. The attached file "CFO services to be put into Thornfield advisory theme", shows the content for the design. The two other files show the theme and colours for the new design.

```html
<!DOCTYPE html>
<html lang="en">
<head>
<meta charset="utf-8">
<title>Thornfield Advisory – CFO Services</title>
<link rel="stylesheet" href="https://fonts.googleapis.com/css2?family=Oswald:wght@500;600;700&display=swap">
<style>
  :root {
    --navy: #02244f;
    --ink: #0b2a5b;
    --sky: #22a8e2;
    --royal: #1750bb;
    --deep: #0b3a8a;
    --orange: #f0922e;
    --paper: #ffffff;
    --disc: #f7f9fd;
  }
  html, body {
    margin: 0;
    padding: 0;
    width: 1200px;
    height: 956px;
    overflow: hidden;
    background: var(--paper);
  }
  .cfo-wheel {
    display: block;
    width: 1200px;
    height: 956px;
  }
  .hub { fill: var(--navy); }
  .petal { stroke: var(--paper); stroke-width: 14; stroke-linejoin: round; }
  .petal--sky { fill: var(--sky); }
  .petal--royal { fill: var(--royal); }
  .petal--deep { fill: var(--deep); }
  .petal--orange { fill: var(--orange); }
  .disc { fill: var(--disc); }
  .arrow line { stroke: var(--paper); stroke-width: 7; }
  .arrow polygon { fill: var(--paper); }
  .label {
    font-family: "Oswald", sans-serif;
    font-weight: 600;
    fill: var(--ink);
    text-anchor: middle;
    font-size: 37px;
    letter-spacing: -0.5px;
  }
  .label--small { font-size: 19px; font-weight: 500; }
  .label--title {
    font-size: 64px;
    font-weight: 700;
    fill: var(--navy);
  }
</style>
</head>
<body>
<svg class="cfo-wheel" viewBox="0 0 2000 1593" xmlns="http://www.w3.org/2000/svg" role="img" aria-label="Chief Financial Officer responsibilities">
  <defs>
    <path id="petal-shape" d="M 0,-236 C -30,-248 -60,-264 -70,-290 L -150,-510 A 155 155 0 1 1 150,-510 L 70,-290 C 60,-264 30,-248 0,-236 Z"/>
    <g id="arrow-shape" class="arrow">
      <line x1="0" y1="-145" x2="0" y2="-180"/>
      <polygon points="-11,-178 11,-178 0,-205"/>
    </g>
  </defs>

  <g class="hub-group" transform="translate(905 768)">
    <circle class="hub" r="252"/>
    <use href="#petal-shape" class="petal petal--sky" transform="rotate(0)"/>
    <use href="#petal-shape" class="petal petal--deep" transform="rotate(45)"/>
    <use href="#petal-shape" class="petal petal--orange" transform="rotate(90)"/>
    <use href="#petal-shape" class="petal petal--royal" transform="rotate(135)"/>
    <use href="#petal-shape" class="petal petal--sky" transform="rotate(180)"/>
    <use href="#petal-shape" class="petal petal--deep" transform="rotate(225)"/>
    <use href="#petal-shape" class="petal petal--orange" transform="rotate(270)"/>
    <use href="#petal-shape" class="petal petal--royal" transform="rotate(315)"/>

    <g class="discs">
      <circle class="disc" cx="0" cy="-550" r="137" transform="rotate(0)"/>
      <circle class="disc" cx="0" cy="-550" r="137" transform="rotate(45)"/>
      <circle class="disc" cx="0" cy="-550" r="137" transform="rotate(90)"/>
      <circle class="disc" cx="0" cy="-550" r="137" transform="rotate(135)"/>
      <circle class="disc" cx="0" cy="-550" r="137" transform="rotate(180)"/>
      <circle class="disc" cx="0" cy="-550" r="137" transform="rotate(225)"/>
      <circle class="disc" cx="0" cy="-550" r="137" transform="rotate(270)"/>
      <circle class="disc" cx="0" cy="-550" r="137" transform="rotate(315)"/>
    </g>

    <g class="arrows">
      <use href="#arrow-shape" transform="rotate(0)"/>
      <use href="#arrow-shape" transform="rotate(45)"/>
      <use href="#arrow-shape" transform="rotate(90)"/>
      <use href="#arrow-shape" transform="rotate(135)"/>
      <use href="#arrow-shape" transform="rotate(180)"/>
      <use href="#arrow-shape" transform="rotate(225)"/>
      <use href="#arrow-shape" transform="rotate(270)"/>
      <use href="#arrow-shape" transform="rotate(315)"/>
    </g>

    <circle class="disc" r="136"/>
  </g>

  <text class="label label--title" x="905" y="727">CHIEF</text>
  <text class="label label--title" x="905" y="788">FINANCIAL</text>
  <text class="label label--title" x="905" y="849">OFFICER</text>

  <text class="label" x="905" y="164">COST</text>
  <text class="label" x="905" y="207">ACCOUNTING &amp;</text>
  <text class="label" x="905" y="251">COST</text>
  <text class="label" x="905" y="295">MANAGEMENT</text>

  <text class="label" x="1293" y="325">CAPTIAL</text>
  <text class="label" x="1293" y="369">STRUCTURE</text>
  <text class="label" x="1293" y="413">AND THE COST</text>
  <text class="label" x="1293" y="457">OF CAPITAL</text>

  <text class="label" x="1453" y="716">LONG-TERM &amp;</text>
  <text class="label" x="1453" y="760">SHORT-TERM</text>
  <text class="label" x="1453" y="804">INVESTMENT</text>
  <text class="label" x="1453" y="848">DECISIONS</text>

  <text class="label" x="1297" y="1149">PERFORMANCE</text>
  <text class="label" x="1297" y="1193">EVALUATION</text>

  <text class="label" x="905" y="1291">BUDGETING &amp;</text>
  <text class="label" x="905" y="1335">STRATEGIC</text>
  <text class="label" x="905" y="1379">PLANNING</text>

  <text class="label" x="514" y="1149">RISK</text>
  <text class="label" x="514" y="1193">MANAGEMENT</text>

  <text class="label" x="355" y="737">COMPLIANCE:</text>
  <text class="label" x="352" y="782">TAX, LEGAL AND</text>
  <text class="label" x="352" y="826">REGULATORY</text>

  <text class="label" x="517" y="367">COMMUNICATION</text>
  <text class="label label--small" x="514" y="393">BOARD OF DIRECTORS,</text>
  <text class="label label--small" x="514" y="417">CREDITORS, OWNERS,</text>
  <text class="label label--small" x="514" y="441">INVESTORS, CREDIT RATING</text>
  <text class="label label--small" x="514" y="464">AGENCIES</text>
</svg>
</body>
</html>
```